Advertisement flyer for fire sprinkler repair parts. The projected audience are contractors.

I need a flyer advertising specific parts that we are stocking at our company "Coastal Valveline Supply." I have attached a picture of our logo. I want the title to say "Fire Pump Repair Parts and Accessories." I want to specifically advertise the following parts: Repack Kits and Repair Parts, Jockey Pumps, Pump Controllers, Casing Relief Valves, Air Release Valves, Suction/Discharge Gauges, Pump Shaft Couplers & Shim Kits, Fire Pump Relief Valves, and UL Listed Pressure Reducing Valves. I have attached pictures of the manufacturers I want to advertise on this flyer. I have also attached pictures of some of the parts we are stocking that I would like to be included somewhere in the flyer. I would like all of the pictures to have a transparent background. Also I would like our phone number :(800)-318-4027, and our website www.valvelinesupply-demo.com included. I made my own design that I have Attached. You do not have to go based off this design, but I would like the basic content to be the same. We do have Same- Day shipping as well as Free Tech Support if you can include that anywhere.

```html
<!DOCTYPE html>
<html lang="en">
<head>
<meta charset="utf-8">
<title>Coastal Valveline Supply – Fire Pump Repair Parts Flyer</title>
<link rel="stylesheet" href="https://fonts.googleapis.com/css2?family=Oswald:wght@400;500&family=Montserrat:wght@500;600;700&display=swap">
<style>
  :root {
    --brand-blue: #2e3a94;
    --band-blue: #33479a;
    --accent-red: #e0174a;
    --ink: #1d1d1f;
    --paper: #ffffff;
    --stage: #e9e9ec;
    --frame: #2b2b2b;
  }
  * { box-sizing: border-box; margin: 0; padding: 0; }
  html, body { width: 1200px; height: 1200px; overflow: hidden; background: var(--stage); }
  .flyer {
    position: absolute; left: 195px; top: 31px;
    width: 942px; height: 1322px;
    background: var(--paper);
    transform: scale(0.86); transform-origin: 0 0;
    font-family: "Montserrat", Arial, sans-serif; color: var(--ink);
  }
  .flyer > * { position: absolute; }

  .brand { left: 58px; top: 48px; display: flex; align-items: center; gap: 14px; }
  .brand-mark { width: 34px; height: 34px; border-radius: 50%; background: var(--brand-blue); }
  .brand-name { font-weight: 500; font-size: 32px; color: var(--brand-blue); letter-spacing: -0.3px; }

  .hero-photo { left: 0; top: 130px; width: 522px; height: 498px;
    background: linear-gradient(135deg, #b9aea6 0%, #c8322d 38%, #a8121a 62%, #d9d2cc 100%); }

  .headline-main { left: 548px; top: 148px; font-family: "Oswald", sans-serif; font-weight: 500;
    font-size: 70px; line-height: 1; color: var(--brand-blue); letter-spacing: -0.5px; }
  .headline-accent { left: 548px; top: 236px; font-weight: 700; font-size: 28px; color: var(--accent-red); letter-spacing: 0.6px; }
  .headline-sub { left: 554px; top: 282px; font-weight: 700; font-size: 28px; color: var(--ink); letter-spacing: 0.6px; }

  .about-title { left: 557px; top: 358px; font-weight: 500; font-size: 27px; color: var(--accent-red); letter-spacing: 0.6px; }
  .about-text { left: 557px; top: 404px; width: 324px; font-size: 13.4px; line-height: 16.6px;
    font-weight: 500; text-align: justify; }

  .section-title { left: 0; width: 100%; top: 676px; text-align: center; font-family: "Oswald", sans-serif;
    font-weight: 400; font-size: 46px; letter-spacing: -1px; color: var(--ink); }

  .parts-band { left: 0; top: 752px; width: 100%; height: 184px; background: var(--band-blue); }
  .parts-list { list-style: none; position: absolute; color: #fff; font-size: 15px; font-weight: 500; letter-spacing: 0.2px; }
  .parts-list li { display: flex; align-items: center; gap: 18px; }
  .parts-list svg { width: 27px; height: 27px; flex: none; }
  .col-1 { left: 30px; top: 30px; } .col-1 li { height: 34px; }
  .col-2 { left: 305px; top: 37px; } .col-2 li { height: 34px; }
  .col-3 { left: 592px; top: 34px; } .col-3 li { height: 31px; }
  .divider { position: absolute; top: 28px; width: 1px; height: 128px; background: rgba(255,255,255,0.8); }

  .product { top: 996px; width: 186px; height: 126px; border: 2px solid var(--frame); }
  .product-pump { left: 51px; background: linear-gradient(90deg, #fff 30%, #d8c8aa 45%, #2e5fa6 52%, #c9ccd2 60%, #fff 72%); }
  .product-set { left: 263px; background: linear-gradient(160deg, #f1f1f1 0%, #c41b22 40%, #a3161b 70%, #e7e7e7 100%); }
  .product-valve { left: 482px; background: radial-gradient(ellipse at 50% 55%, #a88a4e 0%, #c7ab72 22%, #fff 45%); }
  .product-kit { left: 713px; background: linear-gradient(135deg, #b49f8c 0%, #8f8a86 45%, #cfc7bf 100%); }

  .call { left: 0; width: 100%; top: 1170px; text-align: center; font-size: 19px; font-weight: 500; letter-spacing: 1px; }

  .partners { left: 180px; top: 1228px; width: 590px; display: flex; justify-content: space-between; align-items: center; }
  .partner-badge { width: 64px; height: 30px; border-radius: 4px; background: #c9cdd8; }
  .partner-badge.oval { width: 80px; border-radius: 50%; background: #3a54a2; }
  .partner-badge.red { width: 44px; height: 38px; background: #c42026; }

  .website { left: 0; width: 100%; top: 1286px; text-align: center; font-size: 15px; font-weight: 600; letter-spacing: 4.2px; }
  .footer-bar { left: 0; bottom: 0; width: 100%; height: 12px; background: var(--accent-red); }
</style>
</head>
<body>
<main class="flyer">
  <div class="brand">
    <span class="brand-mark"></span>
    <span class="brand-name">Coastal Valveline Supply</span>
  </div>

  <div class="hero-photo" role="img" aria-label="Photo of a fire pump room with red pumps, valves and piping"></div>

  <h1 class="headline-main">COASTAL</h1>
  <p class="headline-accent">VALVELINE BACKFLOW</p>
  <p class="headline-sub">PREVENTER PARTS</p>

  <h2 class="about-title">ABOUT US</h2>
  <p class="about-text">Coastal Valveline Supply is your complete source for backflow preventer repair parts, accessories and enclosures. Founded in 1976, our company is the nation’s leading backflow preventer specialist, trusted by thousands of technicians, plumbing contractors, fire line contractors, irrigation contractors, building managers and city officials across the country. Our dedication to providing the most comprehensive selection of backflow preventer repair parts is second to none and only matched by the knowledge of our highly trained staff.</p>

  <h2 class="section-title">Fire Pump Repair Parts &amp; Accessories!</h2>

  <section class="parts-band">
    <ul class="parts-list col-1">
      <li><svg viewBox="0 0 28 28"><circle cx="14" cy="14" r="12.5" fill="none" stroke="#fff" stroke-width="1.5"/><rect x="9" y="10" width="10" height="9" fill="#fff"/></svg>Fire Pump Repack Kits</li>
      <li><svg viewBox="0 0 28 28"><circle cx="14" cy="14" r="12.5" fill="none" stroke="#fff" stroke-width="1.5"/><rect x="10" y="8" width="7" height="12" fill="none" stroke="#fff" stroke-width="1.5"/></svg>Jockey Pumps</li>
      <li><svg viewBox="0 0 28 28"><circle cx="14" cy="14" r="12.5" fill="none" stroke="#fff" stroke-width="1.5"/><path d="M8 19h12M10 19v-6h4v6M15 19v-9h3v9" fill="none" stroke="#fff" stroke-width="1.5"/></svg>Pump Controllers</li>
      <li><svg viewBox="0 0 28 28"><circle cx="14" cy="14" r="12.5" fill="none" stroke="#fff" stroke-width="1.5"/><path d="M8 18h12M14 8v10M10 12l4-4 4 4" fill="none" stroke="#fff" stroke-width="1.5"/></svg>Casing Relief Valves</li>
    </ul>
    <span class="divider" style="left:276px"></span>
    <ul class="parts-list col-2">
      <li><svg viewBox="0 0 28 28"><circle cx="14" cy="14" r="12.5" fill="none" stroke="#fff" stroke-width="1.5"/><path d="M9 20V8h9v5H9" fill="none" stroke="#fff" stroke-width="1.5"/></svg>Air Release Valves</li>
      <li><svg viewBox="0 0 28 28"><circle cx="14" cy="14" r="12.5" fill="none" stroke="#fff" stroke-width="1.5"/><circle cx="14" cy="14" r="6" fill="none" stroke="#fff" stroke-width="1.5"/><path d="M14 14l3-3" stroke="#fff" stroke-width="1.5"/></svg>Suction / Discharge Gauges</li>
      <li><svg viewBox="0 0 28 28"><circle cx="14" cy="14" r="12.5" fill="none" stroke="#fff" stroke-width="1.5"/><path d="M14 8v5M9 18v-5h10v5" fill="none" stroke="#fff" stroke-width="1.5"/><rect x="12" y="6" width="4" height="3" fill="#fff"/></svg>Flow Meters</li>
    </ul>
    <span class="divider" style="left:573px"></span>
    <ul class="parts-list col-3">
      <li><svg viewBox="0 0 28 28"><circle cx="14" cy="14" r="12.5" fill="none" stroke="#fff" stroke-width="1.5"/><rect x="10" y="8" width="8" height="12" fill="none" stroke="#fff" stroke-width="1.5"/><path d="M10 14h8" stroke="#fff" stroke-width="1.5"/></svg>Pump Shaft Couplers &amp; Shim Kits</li>
      <li><svg viewBox="0 0 28 28"><circle cx="14" cy="14" r="12.5" fill="none" stroke="#fff" stroke-width="1.5"/><path d="M14 7l6 7-6 7-6-7z" fill="none" stroke="#fff" stroke-width="1.5"/></svg>Fire Pump Relief Valves</li>
      <li><svg viewBox="0 0 28 28"><circle cx="14" cy="14" r="12.5" fill="none" stroke="#fff" stroke-width="1.5"/><circle cx="14" cy="14" r="6" fill="none" stroke="#fff" stroke-width="1.5"/><path d="M11 14l2 2 4-4" fill="none" stroke="#fff" stroke-width="1.5"/></svg>UL Listed Pressure Reducing Valves</li>
    </ul>
  </section>

  <div class="product product-pump" role="img" aria-label="Photo of a vertical stainless jockey pump"></div>
  <div class="product product-set" role="img" aria-label="Photo of a red split-case fire pump set"></div>
  <div class="product product-valve" role="img" aria-label="Photo of a bronze pressure reducing valve"></div>
  <div class="product product-kit" role="img" aria-label="Photo of a fire pump repack kit with gaskets and shims"></div>

  <p class="call">CALL US TODAY: (800) 318-4027</p>

  <div class="partners" aria-label="Manufacturers we stock">
    <span class="partner-badge oval"></span>
    <span class="partner-badge"></span>
    <span class="partner-badge red"></span>
    <span class="partner-badge"></span>
    <span class="partner-badge"></span>
    <span class="partner-badge" style="background:#3f63c4"></span>
  </div>

  <p class="website">www.valvelinesupply-demo.com</p>
  <div class="footer-bar"></div>
</main>
</body>
</html>
```